Coastal Learner Bureau business cards

Australian company about to start offering its services. We recruit international students to come to study English, vocational education and postgraduate courses in Australia. We help them find the institution and select the right city they want to come to Australia. We are a young, online oriented and supportive agency. Our clients are between 18 and 35 years old, mainly University students, young professionals or people with work experience. We provide much more information that any other agency offer. We administrate a Facebook group with more than 11.000 members that daily ask questions about general information when coming to Australia, while they are here and even after they leave the country

Target Market(s)

International students from South America, Central America and Europe

Industry/Entity Type

Student

Contact Information for Business Card

Tomas Bilbrea
Managing Director
tomas@kelvarin.com.au
www.kelvoria.com.au
+61 491058264
Melbourne, Australia

Font styles to use
Serif
Sans Serif

Colors

Designer to choose colors to be used in the design.

Requirements
Must have
• Horizontal design
• Standard business card size and shape. If font uses green or yellow colours, they will have to match the ones from the logo
Nice to have
• UPDATE: Use the contents of the green image to design one of the card sides. Use our logo in the background of that side as watermark.
• Passport image, or immigration stamps. A picture of the Yarra River (from Melbourne) would be cool as well.
Should not have
• Non-standard business card size and shape
• Not black as the background colour of any sides as we are not a VIP agency or a hight class service. We are orientes to young people and they like colours, pictures, something attractive.
• Vertical design
• NO YELLOW or BLACK AS THE BACKGROUND COLOUR OF ANY SIDE OF THE BIZ CARD

```html
<!DOCTYPE html>
<html lang="en">
<head>
<meta charset="utf-8">
<title>Coastal Learner Bureau – Business Cards</title>
<link href="https://fonts.googleapis.com/css2?family=Roboto:wght@400;700&family=Roboto+Condensed:wght@500;700&display=swap" rel="stylesheet">
<style>
  :root {
    --backdrop: #2a2a2a;
    --card-white: #f2f2f1;
    --brand-green: #0e5a3a;
    --brand-yellow: #e0b70f;
    --text-grey: #4a4a4a;
    --divider-grey: #9a9a9a;
    --white: #ffffff;
  }
  * { margin: 0; padding: 0; box-sizing: border-box; }
  html, body {
    width: 1200px;
    height: 960px;
    overflow: hidden;
    background: var(--backdrop);
  }
  .canvas {
    position: relative;
    width: 1200px;
    height: 960px;
  }
  .card {
    position: absolute;
    width: 600px;
    height: 343px;
  }
  .card-front {
    left: 314px;
    top: 113px;
    background: var(--card-white);
  }
  .card-back {
    left: 311px;
    top: 472px;
    background: var(--brand-green);
  }
  .front-frame {
    position: absolute;
    inset: 0;
  }
  .wordmark {
    position: absolute;
    font-family: "Roboto", sans-serif;
    font-weight: 700;
    letter-spacing: 0.5px;
    white-space: nowrap;
    transform: translate(-50%, -50%);
  }
  .wordmark-front {
    left: 168px;
    top: 172px;
    font-size: 50px;
    color: var(--brand-green);
  }
  .wordmark-back {
    left: 300px;
    top: 176px;
    font-size: 72px;
    color: var(--white);
  }
  .contact-block {
    position: absolute;
    left: 333px;
    top: 100px;
    font-family: "Roboto", sans-serif;
    color: var(--text-grey);
  }
  .person-name {
    font-family: "Roboto Condensed", sans-serif;
    font-weight: 700;
    font-size: 23px;
    line-height: 24px;
    color: var(--brand-green);
  }
  .person-title {
    font-family: "Roboto Condensed", sans-serif;
    font-weight: 500;
    font-size: 16px;
    line-height: 18px;
    color: var(--brand-yellow);
    letter-spacing: 0.3px;
  }
  .person-city {
    margin-top: 10px;
    font-size: 14.5px;
    line-height: 18px;
  }
  .contact-list {
    list-style: none;
    margin-top: 12px;
    font-size: 14.5px;
    line-height: 19px;
  }
  .contact-label {
    font-weight: 700;
    color: var(--brand-green);
  }
  .tagline {
    position: absolute;
    left: 0;
    right: 0;
    top: 299px;
    display: flex;
    align-items: center;
    justify-content: center;
    gap: 4px;
    font-family: "Roboto", sans-serif;
    font-size: 14px;
    color: var(--white);
  }
  .tagline-rule {
    width: 150px;
    height: 1px;
    opacity: 0.8;
  }
  .tagline-rule-left { background: linear-gradient(to right, transparent, var(--white)); }
  .tagline-rule-right { background: linear-gradient(to left, transparent, var(--white)); }
</style>
</head>
<body>
<main class="canvas">
  <section class="card card-front" aria-label="Business card front">
    <svg class="front-frame" width="600" height="343" viewBox="0 0 600 343" aria-hidden="true">
      <g fill="none" stroke-width="3">
        <path d="M298,15 H16 V328 H298" stroke="var(--brand-green)"/>
        <path d="M302,15 H584 V328 H302" stroke="var(--brand-yellow)"/>
      </g>
      <path d="M16,15 H98 A82,82 0 0 0 16,97 Z" fill="var(--brand-green)"/>
      <path d="M584,328 H520 A64,64 0 0 0 584,264 Z" fill="var(--brand-yellow)"/>
      <line x1="301" y1="95" x2="301" y2="248" stroke="var(--divider-grey)" stroke-width="1.5"/>
    </svg>
    <div class="wordmark wordmark-front">Kelvoria</div>
    <div class="contact-block">
      <h1 class="person-name">TOMAS BILBREA</h1>
      <p class="person-title">MANAGING DIRECTOR</p>
      <p class="person-city">Melbourne, Australia</p>
      <ul class="contact-list">
        <li><span class="contact-label">P:</span> +61 491058264</li>
        <li><span class="contact-label">E:</span> tomas@kelvarin.com.au</li>
        <li><span class="contact-label">W:</span> www.kelvoria.com.au</li>
      </ul>
    </div>
  </section>

  <section class="card card-back" aria-label="Business card back">
    <div class="wordmark wordmark-back">Kelvoria</div>
    <p class="tagline">
      <span class="tagline-rule tagline-rule-left"></span>
      <span>Hacemos más por ti!</span>
      <span class="tagline-rule tagline-rule-right"></span>
    </p>
  </section>
</main>
</body>
</html>
```